Flyer to advertise gutter cleaning throughout the Autumn and winter monthss

I need a new flyer to advertise gutter and driveway cleaning, roof and gutter repairs.

I am an experienced licensed Plumber and Gasfitter looking to broaden my scope of work to gutter cleaning. I am experienced in cleaning gutter and live in a area with large gum trees. I wont something that's clear, eye catching but not too busy.

Flyer requirements: Free roof inspection - no obligation. Gutter Cleaning from $199. Pictures of men using blower or hands to clean roof gutters (no obvious faces) to be included. Australian looking houses.

A mention that 'All general plumbing maintenance' is offered as other services but not too much wording about this as the target is for gutter cleaning.

Phone number: 0427 385 912 (in this format)
Business Name: Larkvale Plumbing & Gasfitting
License: 3175420
ABN: 71364058227
Web: http://larkvaleplumbing.example.site/

Target Market(s)

Elderly - busy working class

Industry/Entity Type

Plumber

Font styles to use
Sans Serif

Colors
0355a3
fbed22
ec1f27
f78f20

Requirements
Must have
• Roof Gutter Cleaning pictures
• Men in protective clothing if possible
Nice to have
• More information:
• Prevent against flooding, mold, rust, rotting and corrosion now!
• Gutter Cleaning Services
• • Remove leaves, sticks, and other debris
• • Clear away clogs
• • Test your downpipes
• • Pinpoint any gutter issues
• • Repair gutter
• With regular service, you can count on your property to be well-protected no matter what the forecast!
Should not have
• Houses that don't look Australian

```html
<!DOCTYPE html>
<html lang="en">
<head>
<meta charset="utf-8">
<title>Larkvale Plumbing &amp; Gasfitting – Gutter &amp; Driveway Cleaning Flyer</title>
<link href="https://fonts.googleapis.com/css2?family=Oswald:wght@500;700&family=Lato:wght@400;700&display=swap" rel="stylesheet">
<style>
  :root {
    --page-bg: #e6e8ea;
    --paper: #ffffff;
    --brand-blue: #0355a3;
    --deep-blue: #1d3a8e;
    --brand-red: #ec1f27;
    --hot-red: #e8205a;
    --brand-yellow: #fbed22;
    --ink-grey: #4a4a4a;
    --price-grey: #545454;
    --box-grey: #cbcbcb;
    --footer-black: #1f1c1d;
  }
  html, body {
    margin: 0;
    width: 1200px;
    height: 1200px;
    overflow: hidden;
    background: var(--page-bg);
  }
  .flyer {
    position: absolute;
    left: 196px;
    top: 30px;
    width: 808px;
    height: 1140px;
    background: var(--paper);
    box-shadow: 0 2px 10px rgba(0,0,0,.15);
  }
  .flyer svg { display: block; width: 808px; height: 1140px; }
  .headline { font-family: "Oswald", "Arial Narrow", sans-serif; font-weight: 700; }
  .headline--grey { fill: var(--ink-grey); }
  .headline--blue { fill: url(#blueText); }
  .offer-free { font-family: "Oswald", sans-serif; font-weight: 700; fill: url(#redText); }
  .offer-sub { font-family: "Oswald", sans-serif; font-weight: 700; fill: var(--deep-blue); }
  .price-label { font-family: "Lato", sans-serif; font-weight: 700; fill: var(--price-grey); }
  .price-from { font-family: "Oswald", sans-serif; font-weight: 700; fill: var(--price-grey); }
  .price-value { fill: var(--hot-red); }
  .brand-name { font-family: "Lato", sans-serif; font-weight: 400; fill: #222; }
  .call-title { font-family: "Lato", sans-serif; font-weight: 400; fill: #333; }
  .call-phone { font-family: "Lato", sans-serif; font-weight: 400; fill: var(--hot-red); }
  .reg-line { font-family: "Lato", sans-serif; font-weight: 400; fill: #333; }
  .reg-line .reg-key { font-weight: 700; }
  .footer-text { font-family: "Lato", sans-serif; font-weight: 400; fill: #fff; }
</style>
</head>
<body>
<div class="flyer">
<svg viewBox="0 0 808 1140" xmlns="http://www.w3.org/2000/svg">
  <defs>
    <linearGradient id="roofPhoto" x1="0" y1="0" x2="1" y2="1">
      <stop offset="0" stop-color="#7d8478"/>
      <stop offset=".45" stop-color="#6f7275"/>
      <stop offset="1" stop-color="#8b8e91"/>
    </linearGradient>
    <linearGradient id="drivePhoto" x1="0" y1="0" x2="0" y2="1">
      <stop offset="0" stop-color="#8ea27a"/>
      <stop offset=".45" stop-color="#b79a93"/>
      <stop offset="1" stop-color="#b3747c"/>
    </linearGradient>
    <linearGradient id="blueText" x1="0" y1="0" x2="0" y2="1">
      <stop offset="0" stop-color="#2b4fae"/>
      <stop offset="1" stop-color="#142c78"/>
    </linearGradient>
    <linearGradient id="redText" x1="0" y1="0" x2="0" y2="1">
      <stop offset="0" stop-color="#f04a73"/>
      <stop offset="1" stop-color="#e01a3c"/>
    </linearGradient>
    <clipPath id="heroClip">
      <path d="M0 0 H808 V250 C700 330 560 430 420 425 C260 420 120 370 0 355 Z"/>
    </clipPath>
    <clipPath id="insetClip">
      <circle cx="622" cy="389" r="150"/>
    </clipPath>
  </defs>

  <!-- hero photo -->
  <g role="img" aria-label="Photo of a gloved hand clearing leaves and debris from a roof gutter beside grey roof shingles" clip-path="url(#heroClip)">
    <rect x="0" y="0" width="808" height="440" fill="url(#roofPhoto)"/>
  </g>

  <!-- hero wave bands -->
  <path class="wave-blue" d="M0 355 C120 370 260 420 420 425 C560 430 700 330 808 250 V268 C700 350 560 448 420 443 C260 440 120 392 0 372 Z" fill="var(--deep-blue)"/>
  <path class="wave-red" d="M230 428 C300 446 360 452 420 450 C520 448 600 420 660 395 C600 432 520 458 420 460 C350 460 290 448 230 428 Z" fill="var(--brand-red)"/>
  <path class="wave-red-right" d="M808 255 C780 280 760 300 740 314 L745 322 C770 306 790 290 808 275 Z" fill="var(--brand-red)"/>

  <!-- inset photo -->
  <circle cx="622" cy="389" r="158" fill="var(--brand-yellow)"/>
  <g role="img" aria-label="Photo of a worker in protective trousers pressure washing a paved driveway" clip-path="url(#insetClip)">
    <rect x="470" y="238" width="305" height="305" fill="url(#drivePhoto)"/>
  </g>

  <!-- brand -->
  <circle cx="91" cy="499" r="46" fill="none" stroke="var(--brand-blue)" stroke-width="10"/>
  <text class="brand-name" x="150" y="506" font-size="21">Larkvale Plumbing &amp; Gasfitting</text>

  <!-- headline stack -->
  <text class="headline headline--grey" x="44" y="612" font-size="40" textLength="306" lengthAdjust="spacingAndGlyphs">GUTTER &amp; DRIVEWAY</text>
  <text class="headline headline--blue" x="44" y="691" font-size="84" textLength="306" lengthAdjust="spacingAndGlyphs">CLEANING</text>
  <text class="headline headline--grey" x="44" y="744" font-size="58" textLength="306" lengthAdjust="spacingAndGlyphs">ROOF &amp; GUTTER</text>
  <text class="headline headline--blue" x="44" y="830" font-size="104" textLength="306" lengthAdjust="spacingAndGlyphs">REPAIRS</text>

  <!-- call box -->
  <rect x="48" y="862" width="302" height="98" rx="12" fill="#fff" stroke="#bdbdbd" stroke-width="2"/>
  <text class="call-title" x="199" y="906" font-size="31" text-anchor="middle">CALL US NOW</text>
  <g class="phone-icon" transform="translate(113 935)">
    <circle r="12" fill="var(--deep-blue)"/>
    <path d="M-5 -6 C-6 -2 -3 4 3 6 L5 3 L2 1 L0 2 C-2 1 -3 -1 -3 -3 L-2 -5 L-4 -7 Z" fill="#fff"/>
  </g>
  <text class="call-phone" x="134" y="944" font-size="28">0427 385 912</text>

  <text class="reg-line" x="199" y="984" font-size="19" text-anchor="middle"><tspan class="reg-key">License:</tspan> 3175420</text>
  <text class="reg-line" x="199" y="1012" font-size="19" text-anchor="middle"><tspan class="reg-key">ABN:</tspan> 71364058227</text>

  <!-- free inspection -->
  <text class="offer-free" x="474" y="667" font-size="108" textLength="215" lengthAdjust="spacingAndGlyphs">FREE</text>
  <text class="offer-sub" x="474" y="703" font-size="33" textLength="215" lengthAdjust="spacingAndGlyphs">ROOF INSPECTION</text>

  <!-- price boxes -->
  <g class="price-box">
    <rect x="418" y="721" width="332" height="131" fill="var(--box-grey)"/>
    <rect x="432" y="735" width="304" height="103" fill="none" stroke="#9e9e9e" stroke-width="1.5" stroke-dasharray="7 5"/>
    <text class="price-label" x="584" y="772" font-size="24" text-anchor="middle" textLength="232" lengthAdjust="spacingAndGlyphs">GUTTER CLEANING</text>
    <text class="price-from" x="584" y="825" font-size="52" text-anchor="middle">FROM <tspan class="price-value">$199</tspan></text>
  </g>
  <g class="price-box">
    <rect x="418" y="874" width="332" height="132" fill="var(--box-grey)"/>
    <rect x="432" y="888" width="304" height="104" fill="none" stroke="#9e9e9e" stroke-width="1.5" stroke-dasharray="7 5"/>
    <text class="price-label" x="584" y="926" font-size="24" text-anchor="middle" textLength="232" lengthAdjust="spacingAndGlyphs">DRIVEWAY CLEANING</text>
    <text class="price-from" x="584" y="977" font-size="52" text-anchor="middle">FROM <tspan class="price-value">$299</tspan></text>
  </g>

  <!-- footer -->
  <path class="footer-band" d="M0 1060 C250 1020 560 1020 808 1080 V1140 H0 Z" fill="var(--footer-black)"/>
  <path class="footer-blue" d="M0 1050 C250 1010 560 1012 808 1068 V1080 C560 1024 250 1022 0 1062 Z" fill="var(--deep-blue)"/>
  <path class="footer-red" d="M0 1040 C250 1000 560 998 808 1056 V1068 C560 1012 250 1010 0 1050 Z" fill="var(--hot-red)"/>
  <text class="footer-text" x="409" y="1079" font-size="15.5" text-anchor="middle">Business Name:</text>
  <text class="footer-text" x="409" y="1099" font-size="15.5" text-anchor="middle">LARKVALE PLUMBING &amp; GASFITTING</text>
</svg>
</div>
</body>
</html>
```